NEW Wordpress Website Design for a Dynamic Long Term Healthcare Company in Hawaii

I would like a new website design for my current company, Marlow Health Collective, which has two different brands - Marlow Homecare and Marlow Senior Living. You can see the current website at www.marlowhealth-example.com. The website should be built using Wordpress Software and the Framewise theme. The website should have a local Hawaii island/tropical feel, but look professional for healthcare. I'm looking for something fresh, and want the designer to select colors, styles, etc.

In the Header, on all pages, I would like a menu that includes Home Care, Senior Living, Rates, and About Us.
Under each of the Header Menu Titles, I would like these drop downs included:
Home Care (drop down pages)- Nurse Aide Care, 24-Hour Home Care, Skilled Nursing, Lifestyle Aide, Hospice at Home, Bathing & Meal Service.
Senior Living (drop down pages) - Long-Term Stay, Short-Term Stay.
Rates (drop down page) - Rates.
About Us (drop down pages) - Our Mission, Ohana Talk, About Dana Marlow.

In the footer, on all pages, you should include the address: 248 Pueo Lane, Suite 310, Honolulu, HI 96817. Phone number: 808-555-0172
The footer should also include buttons for a page called Learn, Caregiver Jobs, and each of the service page links to include: Nurse Aide Care, 24-Hour Home Care, Skilled Nursing, Lifestyle Aide, Hospice at Home, Bathing & Meal Service.
Please don't take the current website and redesign a few aspects. I'm looking for a completely different look and feel.

Target Market(s)

40-80 year olds

Industry/Entity Type

Long Term Healthcare

Coding

Coded - Design and coding required

Requirements
Should not have
• Our existing website as a template. We are looking for a complete redesign. Thank you.

```html
<!DOCTYPE html>
<html lang="en">
<head>
<meta charset="utf-8">
<title>Marlow Health Collective</title>
<link href="https://fonts.googleapis.com/css2?family=Poppins:wght@400;500;600;700&family=DM+Sans:wght@400;500;700&display=swap" rel="stylesheet">
<style>
:root{
  --navy:#14193d;
  --teal:#3fc4cc;
  --teal-dark:#0d6286;
  --ink-blue:#0f5f86;
  --grey:#b5bac2;
  --mint:#f1fbfc;
  --blush:#fff3f3;
  --frame-pink:#fde3e3;
  --white:#ffffff;
}
*{margin:0;padding:0;box-sizing:border-box}
html,body{width:1200px;height:3354px;overflow:hidden}
body{position:relative;background:var(--white);font-family:"Poppins",sans-serif;color:var(--navy)}
.abs{position:absolute}
.band-hero{left:0;top:0;width:1200px;height:840px;background:var(--mint)}
.band-patient{left:0;top:1637px;width:1200px;height:719px;background:var(--mint)}
.band-foot{left:0;top:2356px;width:1200px;height:998px;background:var(--mint)}
.grad-text{background:linear-gradient(90deg,var(--teal),var(--teal-dark));-webkit-background-clip:text;background-clip:text;color:transparent}
.btn{position:absolute;display:flex;align-items:center;justify-content:center;border-radius:30px;color:#fff;font-weight:600;font-size:14px;background:linear-gradient(90deg,#4fd6dc,var(--teal-dark));box-shadow:0 8px 18px rgba(13,98,134,.25)}
.brand{position:absolute;display:flex;align-items:center;gap:8px;font-family:"Poppins",sans-serif;font-weight:600;font-size:17px;color:var(--navy)}
.brand i{display:block;width:12px;height:12px;border-radius:50%;background:var(--teal)}
.nav{position:absolute;top:47px;font-size:15px;font-weight:600;color:var(--ink-blue);display:flex;align-items:center;gap:8px}
.hero-title{left:100px;top:152px;font-size:53px;font-weight:700;line-height:78px;white-space:nowrap}
.hero-copy{left:100px;top:405px;width:395px;font-size:15px;line-height:33px;color:var(--grey)}
.stat{position:absolute;top:645px}
.stat b{display:block;font-size:31px;font-weight:600;line-height:40px}
.stat span{display:block;font-size:16px;line-height:23px;color:var(--grey);font-weight:500}
.section-title{left:0;width:1200px;text-align:center;font-size:42px;font-weight:700;line-height:53px}
.card{position:absolute;top:1075px;width:422px;height:454px;border-radius:22px;box-shadow:0 10px 26px rgba(20,25,61,.07);text-align:center}
.card .pic{width:135px;height:135px;border-radius:50%;margin:52px auto 0}
.card h3{font-size:25px;font-weight:600;margin-top:36px}
.card p{font-family:"DM Sans",sans-serif;font-size:12.5px;line-height:21.7px;margin:22px 36px 0}
.dot{position:absolute;top:2244px;width:18px;height:18px;border-radius:50%;border:2px solid var(--ink-blue)}
.cta{left:100px;top:2414px;width:1000px;height:345px;background:#fff;border-radius:16px;text-align:center}
.foot-col{position:absolute;top:2903px;font-family:"DM Sans",sans-serif}
.foot-col h4{font-family:"Poppins",sans-serif;font-size:15px;font-weight:600;margin-bottom:22px}
.foot-col a{display:block;color:var(--navy);text-decoration:none;font-size:13px;line-height:17px;margin-bottom:21px;width:110px}
.social{position:absolute;top:2980px;width:34px;height:34px;border-radius:50%;background:#dff1f4}
.foot-info{left:166px;font-family:"DM Sans",sans-serif;font-size:13px;line-height:18px}
.foot-info h5{font-family:"Poppins",sans-serif;font-size:14.5px;font-weight:600}
</style>
</head>
<body>

<div class="abs band-hero"></div>

<!-- Header -->
<div class="brand" style="left:98px;top:46px"><i></i>Marlow</div>
<div class="nav" style="left:390px">Home Care <svg width="10" height="6"><path d="M1 1l4 4 4-4" fill="none" stroke="#0f5f86" stroke-width="1.6"/></svg></div>
<div class="nav" style="left:547px">Senior Living <svg width="10" height="6"><path d="M1 1l4 4 4-4" fill="none" stroke="#0f5f86" stroke-width="1.6"/></svg></div>
<div class="nav" style="left:713px">Rates <svg width="10" height="6"><path d="M1 1l4 4 4-4" fill="none" stroke="#0f5f86" stroke-width="1.6"/></svg></div>
<div class="nav" style="left:826px">About Us <svg width="10" height="6"><path d="M1 1l4 4 4-4" fill="none" stroke="#0f5f86" stroke-width="1.6"/></svg></div>
<div class="btn" style="left:963px;top:36px;width:141px;height:45px">Contact Us</div>

<!-- Hero -->
<div class="abs hero-title">Comprehensive<br><span class="grad-text">Care for Your</span><br>Loved Ones</div>
<p class="abs hero-copy">We offer a wide range of professional in-home care services, ensuring comfort and personalized attention for your loved ones. Our dedicated team is here to assist you throughout the entire island.</p>
<div class="btn" style="left:100px;top:558px;width:204px;height:52px">Explore Our Services</div>
<div class="stat" style="left:113px"><b>500+</b><span>Happy Family<br>Served</span></div>
<div class="stat" style="left:250px"><b>200+</b><span>Trained<br>Caregivers</span></div>
<div class="stat" style="left:363px"><b>24/7</b><span>Support and<br>Assistance</span></div>

<div class="abs" style="left:579px;top:112px;width:621px;height:619px;border-radius:220px 0 0 12px;background:linear-gradient(150deg,#cfe9f1,#bfe3ea 60%,#d5eef3)"></div>
<div class="abs" role="img" aria-label="Caregiver serving a meal to an older couple at a dining table" style="left:655px;top:169px;width:430px;height:605px;border-radius:215px 215px 18px 18px;border:16px solid var(--frame-pink);background:linear-gradient(180deg,#d9e59c,#b49a6c 55%,#7c4a2c);box-shadow:0 10px 30px rgba(20,25,61,.12)"></div>

<!-- Services -->
<h2 class="abs section-title" style="top:914px">Our <span class="grad-text">Main Services</span><br>Categories</h2>
<div class="card" style="left:134px;background:var(--blush)">
  <div class="pic" role="img" aria-label="Caregiver helping a man at home" style="background:radial-gradient(circle,#d7dc8a,#9a8a5a)"></div>
  <h3>Home Care</h3>
  <p style="color:var(--navy)">At Marlow Homecare, we provide professional, personalized in-home care services to ensure your loved ones receive the attention they need in the comfort of their own home. From daily assistance with personal care to specialized medical support, our dedicated caregivers are available across the entire island of Oahu to help maintain independence and quality of life.</p>
</div>
<div class="card" style="left:639px;background:var(--mint)">
  <div class="pic" role="img" aria-label="Seniors gathered in a care home living room" style="background:radial-gradient(circle,#c9b58a,#7d6a4e)"></div>
  <h3 style="margin-top:38px">Senior Living</h3>
  <p style="color:var(--ink-blue)">Marlow Senior Living offers a beautiful and serene Adult Residential Care Home located in Kailua, on Oahu's windward side. Here, we provide a comfortable, community-focused living environment for seniors who need more support in their day-to-day lives. With compassionate caregivers and a peaceful setting, your loved ones can enjoy both safety and a sense of belonging.</p>
</div>

<!-- Patient -->
<div class="abs band-patient"></div>
<div class="abs" style="left:117px;top:1849px;font-size:15px;font-weight:500">Our Loved Patient</div>
<div class="abs grad-text" style="left:117px;top:1902px;font-size:42px;font-weight:700;line-height:56px">Keoni Alana</div>
<p class="abs" style="left:117px;top:1988px;width:405px;font-size:15px;line-height:22.8px;color:var(--grey)">At the heart of everything we do are the individuals we care for. Our beloved patients inspire us every day with their resilience and strength.</p>
<div class="btn" style="left:117px;top:2085px;width:172px;height:45px">Join Our Family</div>
<div class="abs" style="left:616px;top:1726px;width:477px;height:467px;background:#fff;border-radius:240px 14px 14px 240px;box-shadow:0 8px 24px rgba(20,25,61,.08)"></div>
<div class="abs" role="img" aria-label="Nurse assisting a smiling older man seated on a bed" style="left:641px;top:1750px;width:428px;height:418px;border-radius:220px 4px 4px 220px;background:linear-gradient(120deg,#e3ed9a,#b8c87a 45%,#6e8fa8)"></div>
<div class="dot" style="left:890px"></div>
<div class="dot" style="left:930px"></div>
<div class="dot" style="left:971px"></div>
<div class="dot" style="left:1011px"></div>
<div class="dot" style="left:1051px;background:var(--ink-blue)"></div>

<!-- CTA -->
<div class="abs band-foot"></div>
<div class="abs cta">
  <h2 style="margin-top:60px;font-size:44px;font-weight:700;line-height:56px">Get <span class="grad-text">started with</span> <span style="font-weight:400;color:var(--ink-blue)">Marlow Care</span></h2>
  <p style="margin:22px auto 0;width:660px;font-size:15.5px;line-height:26px;color:var(--grey)">Whether you're looking for in-home support or a residential care solution, our team at Marlow Care is here to guide you through every step of the process.</p>
</div>
<div class="btn" style="left:513px;top:2643px;width:173px;height:52px">Lets Get Started</div>

<!-- Footer -->
<div class="brand" style="left:166px;top:2924px"><i></i>Marlow</div>
<div class="social" style="left:166px"></div>
<div class="social" style="left:206px"></div>
<div class="social" style="left:246px"></div>
<div class="social" style="left:286px"></div>
<div class="abs foot-info" style="top:3046px"><h5>Our Address</h5><p style="margin-top:10px">248 Pueo Lane, Suite 310,<br>Honolulu, HI 96817</p></div>
<div class="abs foot-info" style="top:3138px"><h5>For General Enquiries</h5><p style="margin-top:12px">Phone Number: 808-555-0172</p></div>

<div class="foot-col" style="left:409px"><h4>Home Care</h4><a>Nurse Aide Care</a><a>24-Hour Home Care</a><a>Skilled Nursing</a><a>Lifestyle Aide</a><a>Hospice at Home</a><a>Bathing &amp; Meal Service</a></div>
<div class="foot-col" style="left:571px"><h4>Senior Living</h4><a>Long-Term Stay</a><a>Short-Term Stay</a></div>
<div class="foot-col" style="left:734px"><h4>Rates</h4><a>Rates</a></div>
<div class="foot-col" style="left:897px"><h4>About Us</h4><a>Our Mission</a><a>Ohana Talk</a><a>About Dana Marlow</a><a>Learn</a><a>Caregiver Jobs</a></div>

<div class="abs" style="left:0;top:3270px;width:1200px;text-align:center;font-family:'DM Sans',sans-serif;font-size:13px;font-weight:500">Copyright © 2024. Marlow Health Collective. All rights reserved.</div>

</body>
</html>
```